Homemaking training schools needs a Business Card design

Designer, Hello!

No special requirements, good-looking enough.
--------------------------------------------------------------------------

Name: Marcus Dole
Chairman
Tel: 0574-71948263
Mobile: 13857420916
Email: kelvora@mailnest.example
Web: www.prt2019.example
Add: No.258, LanpingJie, BeiyuanQu, Ningbo, Zhejiang

LOGO
Ningbo PRT Homemaking Training School

Target Market(s)

pregnant women, mothers, infants, the elderly and families, including cleaning, cooking, nursing training.

Industry/Entity Type

Business

Contact Information for Business Card

Name: Marcus Dole
Chairman
Tel: 0574-71948263
Mobile: 13857420916
Email: kelvora@mailnest.example
Web: www.prt2019.example

LOGO

Font styles to use
Serif
Sans Serif
Decorative

Requirements
Nice to have
• Feels: clean, specifications, safety, comfort, warmth and happiness.

```html
<!DOCTYPE html>
<html lang="en">
<head>
<meta charset="utf-8">
<title>PeiRuiTang Business Card</title>
<link rel="stylesheet" href="https://fonts.googleapis.com/css2?family=Arimo:wght@400;700&display=swap">
<style>
  :root {
    --magenta: #ec1c8c;
    --blue: #1d78c1;
    --blue-light: #3a97d8;
    --ink: #4a4a4a;
    --paper: #ffffff;
    --backdrop: #e9e6e1;
  }
  * { margin: 0; padding: 0; box-sizing: border-box; }
  html, body {
    width: 1200px; height: 950px; overflow: hidden;
    background: var(--backdrop);
    font-family: "Arimo", Arial, sans-serif;
  }
  .canvas { position: relative; width: 1200px; height: 950px; }
  .card {
    position: absolute; width: 600px; height: 343px;
    box-shadow: 0 10px 28px rgba(0,0,0,.22);
    overflow: hidden;
  }
  /* Front */
  .card-front { left: 60px; top: 70px; background: var(--magenta); color: var(--paper); }
  .front-brand {
    position: absolute; left: 0; right: 0; top: 92px;
    display: flex; align-items: center; justify-content: center; gap: 14px;
  }
  .brand-dot { width: 20px; height: 20px; border-radius: 50%; background: currentColor; }
  .front-name { font-size: 54px; font-weight: 700; letter-spacing: .5px; }
  .front-tagline {
    position: absolute; left: 0; right: 0; top: 168px;
    text-align: center; font-size: 20px; letter-spacing: 1px;
  }
  .front-rule {
    position: absolute; left: 140px; right: 140px; top: 202px;
    height: 2px; background: var(--paper);
  }
  .front-web {
    position: absolute; left: 0; right: 0; top: 258px;
    text-align: center; font-size: 17px; letter-spacing: 5px;
  }
  /* Back */
  .card-back { left: 540px; top: 520px; background: var(--paper); }
  .back-band {
    position: absolute; right: 0; top: 0; width: 175px; height: 100%;
    background: linear-gradient(160deg, var(--blue-light), var(--blue));
  }
  .back-brand { position: absolute; left: 36px; top: 40px; display: flex; align-items: center; gap: 10px; color: var(--blue); }
  .back-brand .brand-dot { width: 14px; height: 14px; background: var(--magenta); }
  .back-name { font-size: 38px; font-weight: 700; }
  .back-tagline { position: absolute; left: 150px; top: 88px; font-size: 14px; color: var(--ink); letter-spacing: .5px; }
  .back-rule { position: absolute; left: 36px; top: 110px; width: 340px; height: 1.5px; background: var(--ink); }
  .person { position: absolute; left: 36px; top: 126px; }
  .person-name { font-size: 22px; font-weight: 700; color: var(--blue); }
  .person-title { font-size: 16px; color: var(--magenta); margin-top: 3px; }
  .address { position: absolute; left: 36px; top: 184px; font-size: 14px; line-height: 19px; color: var(--ink); }
  .contacts { position: absolute; left: 36px; top: 228px; list-style: none; font-size: 14px; color: var(--ink); }
  .contacts li { display: flex; align-items: center; gap: 9px; height: 21px; }
  .contacts svg { width: 14px; height: 14px; fill: var(--blue); flex: none; }
</style>
</head>
<body>
<div class="canvas">
  <section class="card card-front">
    <div class="front-brand"><span class="brand-dot"></span><span class="front-name">PeiRuiTang</span></div>
    <div class="front-tagline">Training &amp; Services</div>
    <div class="front-rule"></div>
    <div class="front-web">www.prt2019.example</div>
  </section>

  <section class="card card-back">
    <div class="back-band"></div>
    <div class="back-brand"><span class="brand-dot"></span><span class="back-name">PeiRuiTang</span></div>
    <div class="back-tagline">Training &amp; Services</div>
    <div class="back-rule"></div>
    <div class="person">
      <div class="person-name">Marcus Dole</div>
      <div class="person-title">Chairman</div>
    </div>
    <div class="address">No.258, LanpingJie,<br>BeiyuanQu, Ningbo, Zhejiang</div>
    <ul class="contacts">
      <li><svg viewBox="0 0 16 16"><path d="M3 1l3 3-1.5 2a8 8 0 0 0 5.5 5.5L12 10l3 3-2 2C6 15 1 10 1 3z"/></svg>0574-71948263</li>
      <li><svg viewBox="0 0 16 16"><path d="M4 0h8a1 1 0 0 1 1 1v14a1 1 0 0 1-1 1H4a1 1 0 0 1-1-1V1a1 1 0 0 1 1-1zm1 2v10h6V2zm3 11a1 1 0 1 0 0 2 1 1 0 0 0 0-2z"/></svg>13857420916</li>
      <li><svg viewBox="0 0 16 16"><path d="M0 3h16v1L8 9 0 4zm0 3l8 5 8-5v7H0z"/></svg>kelvora@mailnest.example</li>
      <li><svg viewBox="0 0 16 16"><circle cx="8" cy="8" r="7.5"/></svg>www.prt2019.example</li>
    </ul>
  </section>
</div>
</body>
</html>
```